Business Card for Dental Office - "online review card"

I would like to develop a tasteful card (that would compliment my existing business card) that provides my patients a written link to a portal on my website that would facilitate the generation of online reviews.

My existing business card was a Lumaquarry project a few years ago and has been well received. I hope that it is easily accessed online for reference.

Target Market(s)

Existing patients who need guidance in accessing the "write a review" section of my website

Industry/Entity Type

Business

Requirements
Must have
• -a similar look to my existing card:
http://www.lumaquarry.com.au/contest.aspx?id=5192&page=3

-a link to the following url in writing:
http://www.tessaroldental.com/reviews.html

- a reference to "appreciating feedback" or "how are we doing?"

```html
<!DOCTYPE html>
<html lang="en">
<head>
<meta charset="utf-8">
<title>Daniel R. Tessarol, DDS – Review Card</title>
<link rel="stylesheet" href="https://fonts.googleapis.com/css2?family=Montserrat:wght@400&family=Open+Sans:wght@400;700&display=swap">
<style>
  :root {
    --backdrop: #bdbdbd;
    --card: #ffffff;
    --navy: #2d2f80;
    --navy-deep: #24266b;
    --violet: #4b4da8;
    --ink: #5a5a5a;
    --ink-soft: #6e6e6e;
    --frame: #8a8a8a;
  }
  * { margin: 0; padding: 0; box-sizing: border-box; }
  html, body { width: 1200px; height: 725px; overflow: hidden; }
  body { background: var(--backdrop); position: relative; font-family: "Montserrat", sans-serif; }

  .card {
    position: absolute;
    width: 539px; height: 306px;
    background: var(--card);
    border-radius: 9px;
    overflow: hidden;
  }
  .card--review { left: 330px; top: 36px; }
  .card--front  { left: 42px;  top: 383px; }
  .card--back   { left: 619px; top: 383px; }

  .wave { position: absolute; inset: 0; width: 100%; height: 100%; }

  .brand-mark {
    position: absolute;
    background: linear-gradient(160deg, var(--violet), var(--navy));
    border: 3px solid var(--frame);
  }
  .mark-backing { position: absolute; background: var(--card); border-radius: 12px; left: 43px; top: 70px; width: 113px; height: 112px; }

  .practice-name { position: absolute; color: var(--ink); font-weight: 400; white-space: nowrap; letter-spacing: -0.3px; }
  .practice-name .degree { font-size: 0.62em; letter-spacing: 0; }
  .practice-sub { position: absolute; color: var(--ink-soft); font-size: 11px; letter-spacing: 3px; white-space: nowrap; }

  /* review card */
  .card--review .brand-mark { left: 59px; top: 85px; width: 81px; height: 81px; border-radius: 11px; }
  .card--review .practice-name { left: 164px; top: 88px; font-size: 25px; }
  .card--review .practice-sub { right: 80px; top: 118px; }
  .review-url {
    position: absolute; left: 0; right: 0; top: 209px;
    text-align: center; color: #fff;
    font-family: "Open Sans", sans-serif; font-weight: 700; font-size: 19px;
  }
  .review-prompt {
    position: absolute; left: 0; right: 0; top: 249px;
    text-align: center; color: #fff;
    font-family: "Open Sans", sans-serif; font-size: 17px;
  }

  /* front card */
  .card--front .brand-mark { left: 176px; top: 38px; width: 183px; height: 183px; border-radius: 24px; border-width: 4px; }
  .card--front .practice-name { left: 0; right: 0; top: 232px; text-align: center; font-size: 17px; }
  .card--front .practice-sub { left: 0; right: 0; top: 257px; text-align: center; font-size: 6.5px; letter-spacing: 1.6px; }

  /* back card */
  .card--back .brand-mark { left: 38px; top: 116px; width: 94px; height: 95px; border-radius: 12px; }
  .card--back .practice-name { left: 162px; top: 117px; font-size: 29px; }
  .card--back .practice-sub { right: 33px; top: 156px; }
</style>
</head>
<body>

<section class="card card--review">
  <svg class="wave" viewBox="0 0 539 306" aria-hidden="true">
    <defs>
      <linearGradient id="band" x1="0" y1="0" x2="0" y2="1">
        <stop offset="0" stop-color="#34368c"/>
        <stop offset="1" stop-color="#2a2c78"/>
      </linearGradient>
    </defs>
    <path d="M0 128 C120 178 300 150 539 176 L539 183 C300 160 130 188 0 142 Z" fill="var(--violet)"/>
    <path d="M0 150 C150 200 340 170 539 196 L539 306 L0 306 Z" fill="url(#band)"/>
  </svg>
  <div class="mark-backing"></div>
  <div class="brand-mark"></div>
  <p class="practice-name">Daniel R. Tessarol<span class="degree">, DDS</span></p>
  <p class="practice-sub">AND ASSOCIATES</p>
  <p class="review-url">http://www.tessaroldental.com/reviews.html</p>
  <p class="review-prompt">APPRECIATING FEEDBACK</p>
</section>

<section class="card card--front">
  <div class="brand-mark"></div>
  <p class="practice-name">Daniel R. Tessarol<span class="degree">, DDS</span></p>
  <p class="practice-sub">FAMILY AND COSMETIC DENTISTRY</p>
</section>

<section class="card card--back">
  <div class="brand-mark"></div>
  <p class="practice-name">Daniel R. Tessarol<span class="degree">, DDS</span></p>
  <p class="practice-sub">AND ASSOCIATES</p>
</section>

</body>
</html>
```